Systems and Technology Consultants - Website

Design & Build a website for a new company which operates in the Systems and Technology space for Transportation, Government and Commercial sectors.

Overall design should be minimalist in nature.
Should also have a feed that provides news and event updates on the main page.
Logo has already been awarded and should be incorporated into the site.

We like the overall layout, functionality and simplicity of the below sites. Submitted designs could be similar to or a combination of the aspects on these sites, or perhaps a whole different concept - we are open to new ideas.
Norvique.com
Teblo.it

Update 1 Dated 27 May 2014

All I am moving away from the Teblo.it website and would like it to be more aligned with Norvique.com not only in layout but in functionality. I will be extending the deadline of this design brief for two weeks to incorporate additional requirements and will add addtional funding to the project.

Apologies for not having more information available to provide but with so many submissions its getting confusing.

Thanks Derek

Please note that the brief has been updated and the deadline has been extended.

Important: We will need two language versions of the website, English and Arabic; the website is hosted on HostPelican

Hello All, Thank you for your submissions. We have narrowed it down to the final 6 designers and I just wanted to take a moment and provide a bit of feedback regarding the concepts that we like and the modifications we are looking for. First, let me mention some of the design functions we like. - At the top of the homepage we really like the "region" or "language" tab so that the website can be viewed in both English and Arabic. - We like the homepage to have clear color variation so that the different sections of the homepage are distinct. Additionally, we like the bottom portion of the homepage to be in red. We feel that draws attention to our contact information. Again, we would like the colors to integrate black, gray-scale, red, etc. - Having a search tab at the top of the home page, or integrated into the main image, so that the site is easy to navigate. - We especially like the main image to have the scrolling tabs at the bottom so it is easy to browse the services offered (Consultancy, Solutions Architecture, Masters Systems Integration, Independent Design Review). - In regards to the services offered tab we really like the idea that a few people presented that have the outside of our logo with an icon in the middle of consultancy, solutions, etc., etc. Secondly, as mentioned in our brief we really enjoy the design of norvique site. Specially, we enjoy the strong iconic images they use, the way the tabs at the top scroll easily, and contact us page that generates an email. Lastly, I've included some photos of the concept we have been working on. What we are trying to demonstrate is how our company offers a range of services that are essentially linked together. We provide individual services that when combined present the full service package. We would like this concept to be integrated into the over concept of our website. Please feel free to ask for clarification of any of the above points or contact us if you have any additional questions. We appreciate all of your hard work and are very excited to see the updated designs. Best, Marta Vennick Quelbrant Senior Program Manager marta.vennick@quelbrant-example.com

Industry/Entity Type

Government

Font styles to use
Serif
Sans Serif

Requirements
Must have
• Must work on/adapt to various/mobile devices (responsive)
Must be simple and straightforward
Colors should be in line/matching with logo
2 language versions: English and Arabic (no Thai)
Services should be the first group/row of items after/below the main image
Note: the website will be hosted by hostpelican
Nice to have
• Submit feedback form
What's New section
The banner at the bottom of the site should not be too large; we would like a narrow one more
It would be nice if the header/top banner (with Home, About, etc. tabs) could stay in place as you scroll down (like Norvique and Chatterloop)
We will likely only use one image with a Company slogan on the Home page rather than a carousel of images to rotate through
Should not have
• This is the existing website: http://www.quelbrant-example.org
We do not like the animation, the way the banner icons/titles bounce
Not simple enough, we don't like the functionality or how pages load so slowly
We do not like the logo centered - it should be at the left
The banner and its tabs should not be towards the right, we would like them to be centered, to go all the way across and to be below the logo

```html
<!DOCTYPE html>
<html lang="en">
<head>
<meta charset="utf-8">
<title>Quelbrant International — Integrated Systems</title>
<link href="https://fonts.googleapis.com/css2?family=Open+Sans:wght@300;400;600;700&family=Montserrat:wght@600;700&display=swap" rel="stylesheet">
<style>
:root{
  --red:#e3262b;
  --red-footer:#d42a2a;
  --ink:#1e1e1e;
  --text:#333;
  --muted:#8a8a8a;
  --topbar:#2b2b2b;
  --bottombar:#1d1d1d;
  --panel:#f1f0f0;
  --panel-dark:#3a3a3a;
  --line:#d9d9d9;
  --white:#fff;
}
*{box-sizing:border-box;margin:0;padding:0}
html,body{width:785px;height:1200px;overflow:hidden;background:var(--white)}
body{position:relative;font-family:'Open Sans',sans-serif;color:var(--text)}
a{color:inherit;text-decoration:none}
.abs{position:absolute}

/* top utility bar */
.utility-bar{left:0;top:0;width:785px;height:16px;background:var(--topbar);color:#eee;font-size:8.5px;line-height:16px}
.utility-links{left:73px;top:0}
.utility-links span{margin:0 6px}
.utility-contact{right:72px;top:0;display:flex;gap:20px;align-items:center}
.utility-contact svg{vertical-align:-1px;margin-right:5px}

/* header */
.brand{left:72px;top:40px;display:flex;align-items:center;gap:8px}
.brand-square{width:22px;height:22px;background:var(--red)}
.brand-name{font-family:'Open Sans',sans-serif;font-weight:700;color:var(--red);font-size:15px;letter-spacing:2px;line-height:1.1}
.lang{left:436px;top:31px;display:flex;align-items:center;gap:8px;font-size:11px;color:#555}
.lang-globe{width:22px;height:14px;border-radius:7px;background:var(--red)}
.search{left:530px;top:27px;width:183px;height:22px;border:1px solid #e3e3e3;background:#f5f5f5;border-radius:2px}
.search svg{position:absolute;right:8px;top:5px}
.main-nav{left:294px;top:78px;display:flex;font-size:9.5px;color:var(--ink)}
.main-nav a{padding:2px 0 8px;margin-right:0}
.main-nav .current{color:var(--red);border-bottom:2px solid var(--red);padding:2px 7px 8px}

/* hero */
.hero{left:0;top:111px;width:785px;height:288px;background:linear-gradient(100deg,#5aaccd 0%,#6bb7d6 45%,#8cc9e2 75%,#b9deee 100%)}
.hero-visual{position:absolute;right:0;top:0;width:420px;height:288px;background:radial-gradient(ellipse at 60% 55%,rgba(255,255,255,.45),rgba(255,255,255,0) 65%)}
.hero-title{left:71px;top:78px;font-family:'Montserrat',sans-serif;font-weight:700;color:var(--white);font-size:25px;line-height:35px;letter-spacing:1px}
.hero-title em{font-style:normal;color:var(--red)}
.hero-lede{left:72px;top:153px;width:330px;color:var(--white);font-size:15px;line-height:18px;font-weight:400}
.hero-lede strong{color:var(--red);font-weight:600}
.btn-learn{left:72px;top:202px;width:123px;height:26px;background:var(--red);color:var(--white);border-radius:3px;font-family:'Montserrat',sans-serif;font-weight:700;font-size:8.5px;letter-spacing:1.5px;display:flex;align-items:center;justify-content:center;gap:10px}
.hero-shadow{left:20px;top:399px;width:745px;height:14px;background:radial-gradient(ellipse at 50% 0,rgba(0,0,0,.22),rgba(0,0,0,0) 70%)}

/* services */
.section-title{left:0;top:418px;width:785px;text-align:center;font-size:22px;font-weight:300;color:#333}
.carousel-btn{top:427px;width:25px;height:25px;border-radius:50%;background:#5e5e5e;display:flex;align-items:center;justify-content:center}
.service{top:472px;width:210px;text-align:center}
.service + .service{}
.service-divider{top:470px;width:16px;height:210px;background:linear-gradient(90deg,rgba(0,0,0,.05),rgba(0,0,0,0))}
.service-icon{width:66px;height:66px;margin:0 auto;border-radius:50%;border:4px solid #cfcfcf;display:flex;align-items:center;justify-content:center}
.service-icon.active{border-color:var(--red)}
.service h3{font-weight:400;font-size:12.5px;color:#222;margin-top:13px}
.service p{font-size:8.4px;line-height:13px;color:var(--muted);margin:13px auto 0;width:185px}
.btn-read{display:inline-block;margin-top:20px;border:1.5px solid #333;font-size:8.5px;color:#222;padding:3px 8px;background:var(--white)}
.btn-read.active{border-color:var(--red);color:var(--red)}

/* articles */
.block-title{top:709px;font-size:14px;font-weight:400;color:#333}
.accordion{left:84px;top:738px;width:302px}
.acc-item{display:flex;background:var(--panel);margin-bottom:7px}
.acc-toggle{width:26px;flex:none;background:var(--panel-dark);display:flex;align-items:flex-start;justify-content:center;color:var(--white);font-size:16px;font-weight:300;line-height:1}
.acc-item.open{background:var(--panel)}
.acc-item.open .acc-toggle{background:#d5d5d5;position:relative}
.acc-item.open .acc-toggle::before{content:"";position:absolute;left:0;top:0;width:26px;height:37px;background:var(--red)}
.acc-item.open .acc-toggle span{position:relative;z-index:1;margin-top:8px}
.acc-body{padding:13px 10px 8px 10px}
.acc-body h4{font-weight:400;font-size:10.5px;line-height:13px;color:#222}
.acc-body p{font-size:8px;line-height:13px;color:#8a8a8a;margin-top:8px}
.acc-item.closed .acc-toggle{align-items:center}
.acc-item.closed .acc-body{padding:0 9px;display:flex;align-items:center;font-size:9.5px;color:#222}

/* news */
.news-list{left:428px;top:737px;width:290px}
.news-item{position:absolute;left:0;display:flex;gap:10px}
.date{width:39px;flex:none;text-align:center;color:var(--white)}
.date .day{background:#333;font-size:15px;line-height:18px}
.date .month{background:var(--red);font-size:13px;line-height:17px;border-bottom:2px solid #a61c1c}
.news-item h4{font-weight:400;font-size:11px;color:#222;line-height:13px}
.news-item p{font-size:8.3px;line-height:13px;color:#8a8a8a;margin-top:3px;width:225px}

/* footer */
.footer{left:0;top:1018px;width:785px;height:150px;background:var(--red-footer);color:var(--white)}
.footer-brand{left:72px;top:30px;display:flex;align-items:center;gap:8px}
.footer-brand .brand-square{background:var(--white)}
.footer-brand .brand-name{color:var(--white)}
.footer-about{left:76px;top:76px;width:195px;font-size:8.8px;line-height:13px}
.footer h5{font-size:9.5px;font-weight:600;letter-spacing:.2px}
.sitemap{left:280px;top:26px}
.sitemap ul{list-style:none;margin-top:12px;font-size:6.8px;font-weight:600;line-height:13.2px;padding-left:6px}
.events{left:385px;top:26px}
.events ul{list-style:none;margin-top:11px;font-size:8.6px;line-height:17.6px}
.events li::before{content:"";display:inline-block;width:6px;height:6px;border:1.5px solid var(--white);transform:rotate(45deg);margin:0 9px 1px 4px}
.contact{left:565px;top:22px}
.contact ul{list-style:none;margin-top:10px;font-size:8.4px;font-weight:600;line-height:20.5px}
.contact li{display:flex;align-items:center;gap:9px}
.contact li .ico{width:10px;display:flex;justify-content:center}
.contact li.indent{padding-left:19px}
.bottom-bar{left:0;top:1168px;width:785px;height:32px;background:var(--bottombar);color:#ddd;font-size:9px;line-height:32px}
.copyright{left:71px;top:0}
.follow{right:72px;top:0;display:flex;align-items:center;gap:6px;font-size:10.5px}
.follow .label{margin-right:6px}
.social-dot{width:15px;height:15px;border-radius:50%;background:#4a4a4a}
</style>
</head>
<body>

<div class="utility-bar abs">
  <div class="utility-links abs"><a href="#">Terms</a><span>|</span><a href="#">Privacy Policy</a></div>
  <div class="utility-contact abs">
    <span><svg width="7" height="8" viewBox="0 0 10 12"><path d="M2 0l2 3-1.3 1.3c.6 1.6 1.8 3 3.3 3.8L7.3 6.9 10 9l-1.4 2.5C4 11 0 6 0 1.4z" fill="#fff"/></svg>+123 555 0142</span>
    <span><svg width="10" height="7" viewBox="0 0 12 8"><rect width="12" height="8" fill="#fff"/><path d="M0 0l6 4.5L12 0" stroke="#2b2b2b" fill="none"/></svg>info@quelbrant-example.com</span>
  </div>
</div>

<header>
  <a class="brand abs" href="#"><span class="brand-square"></span><span class="brand-name">QUELBRANT<br>INTERNATIONAL</span></a>
  <div class="lang abs"><span class="lang-globe"></span><span>English</span><svg width="7" height="6" viewBox="0 0 8 6"><path d="M0 0h8L4 6z" fill="#e3262b"/></svg></div>
  <div class="search abs"><svg width="10" height="10" viewBox="0 0 12 12"><circle cx="5" cy="5" r="3.8" stroke="#222" stroke-width="1.8" fill="none"/><path d="M8 8l3 3" stroke="#222" stroke-width="2"/></svg></div>
  <nav class="main-nav abs">
    <a class="current" href="#">HOME</a>
    <a href="#" style="margin-left:22px">Business Units</a>
    <a href="#" style="margin-left:35px">Services</a>
    <a href="#" style="margin-left:33px">About Us</a>
    <a href="#" style="margin-left:33px">Locations</a>
    <a href="#" style="margin-left:33px">Contact Us</a>
  </nav>
</header>

<section class="hero abs">
  <div class="hero-visual" role="img" aria-label="Photo of a businesswoman touching a holographic interface with floating data charts"></div>
  <h1 class="hero-title abs">INTEGRATED <em>SYSTEMS</em><br>RELIABLE SOLUTIONS</h1>
  <p class="hero-lede abs"><strong>QUELBRANT</strong> Specializes in delivering quality fessional Services and Technical Projects that</p>
  <a class="btn-learn abs" href="#">LEARN MORE <svg width="18" height="9" viewBox="0 0 18 9"><path d="M1 1l4 3.5L1 8M8 1l4 3.5L8 8" stroke="#fff" stroke-width="1.3" fill="none"/></svg></a>
</section>
<div class="hero-shadow abs"></div>

<h2 class="section-title abs">Services offered</h2>
<a class="carousel-btn abs" style="left:651px" href="#"><svg width="6" height="7" viewBox="0 0 6 8"><path d="M6 0v8L0 4z" fill="#fff"/></svg></a>
<a class="carousel-btn abs" style="left:687px" href="#"><svg width="6" height="7" viewBox="0 0 6 8"><path d="M0 0v8l6-4z" fill="#fff"/></svg></a>

<div class="service-divider abs" style="left:288px"></div>
<div class="service-divider abs" style="left:498px"></div>

<article class="service abs" style="left:76px">
  <div class="service-icon active"><svg width="26" height="22" viewBox="0 0 26 22"><circle cx="9" cy="6" r="4" fill="#e3262b"/><circle cx="17" cy="6" r="4" fill="#e3262b"/><path d="M1 21c0-6 4-9 8-9s8 3 8 9zM10 21c0-6 3-9 7-9s8 3 8 9z" fill="#e3262b"/></svg></div>
  <h3>Consultancy</h3>
  <p>Lorem Ipsum is simply dummy text of the printing and typesetting industry. Lorem Ipsum has been the industry's standard dummy text ever since the 1500s.</p>
  <a class="btn-read active" href="#">Read More</a>
</article>
<article class="service abs" style="left:286px">
  <div class="service-icon"><svg width="24" height="24" viewBox="0 0 24 24"><circle cx="12" cy="12" r="7" stroke="#cfcfcf" stroke-width="4" stroke-dasharray="3 2.5" fill="none"/><circle cx="12" cy="12" r="2.5" fill="#cfcfcf"/></svg></div>
  <h3>Solutions Architecture</h3>
  <p>Lorem Ipsum is simply dummy text of the printing and typesetting industry. Lorem Ipsum has been the industry's standard dummy text ever since the 1500s.</p>
  <a class="btn-read" href="#">Read More</a>
</article>
<article class="service abs" style="left:496px">
  <div class="service-icon"><svg width="26" height="22" viewBox="0 0 26 22"><path d="M3 18h20v3H3zM6 18V9l6-6 4 4-3 3v8z" fill="#cfcfcf"/></svg></div>
  <h3>Masters Systems Integration</h3>
  <p>Lorem Ipsum is simply dummy text of the printing and typesetting industry. Lorem Ipsum has been the industry's standard dummy text ever since the 1500s.</p>
  <a class="btn-read" href="#">Read More</a>
</article>

<h2 class="block-title abs" style="left:86px">Articles</h2>
<div class="accordion abs">
  <div class="acc-item open">
    <div class="acc-toggle"><span>—</span></div>
    <div class="acc-body">
      <h4>Lorem ipsum dolor sit amet, consectetur adipisicing elit</h4>
      <p>Lorem Ipsum is simply dummy text of the printing and typesetting industry. Lorem Ipsum has been the industry's standard dummy text ever since the 1500s, when an unknown printer took a galley of type and scrambled it to make a type specimen book. It has survived not only five centuries, but also the leap into electronic typesetting, remaining essentially unchanged. It was popularised in the 1960s.</p>
    </div>
  </div>
  <div class="acc-item closed" style="height:26px"><div class="acc-toggle">+</div><div class="acc-body">Lorem ipsum dolor sit amet, consectetur adipisicing elit</div></div>
  <div class="acc-item closed" style="height:26px"><div class="acc-toggle">+</div><div class="acc-body">Lorem ipsum dolor sit amet,</div></div>
  <div class="acc-item closed" style="height:38px"><div class="acc-toggle">+</div><div class="acc-body">Lorem ipsum dolor sit amet, consectetur adipisicing elit</div></div>
</div>

<h2 class="block-title abs" style="left:427px">News</h2>
<div class="news-list abs">
  <div class="news-item" style="top:3px"><div class="date"><div class="day">27</div><div class="month">Feb</div></div><div><h4>Lorem ipsum dolor sit amet,</h4><p>Lorem Ipsum is simply dummy text of the printing and typesetting industry</p></div></div>
  <div class="news-item" style="top:70px"><div class="date"><div class="day">23</div><div class="month">Feb</div></div><div><h4>Lorem ipsum dolor sit amet,</h4><p>Lorem Ipsum is simply dummy text of the printing and typesetting industry</p></div></div>
  <div class="news-item" style="top:138px"><div class="date"><div class="day">22</div><div class="month">Feb</div></div><div><h4>Lorem ipsum dolor sit amet,</h4><p>Lorem Ipsum is simply dummy text of the printing and typesetting industry. Lorem Ipsum has been the industry's standard dummy text</p></div></div>
  <div class="news-item" style="top:209px"><div class="date"><div class="day">23</div><div class="month">Feb</div></div><div><h4>Lorem ipsum dolor sit amet,</h4><p>Lorem Ipsum is simply dummy text of the printing and typesetting industry</p></div></div>
</div>

<footer class="footer abs">
  <div class="footer-brand abs"><span class="brand-square"></span><span class="brand-name">QUELBRANT<br>INTERNATIONAL</span></div>
  <p class="footer-about abs">Lorem ipsum dolorSit amet consecteturAdipsic-ing elit,ed do euismodTempor incidunt Labore et dolorMagna aliqua.Lorem ipsum dolorSit amet consecteturAdipsicing elit,</p>
  <div class="sitemap abs">
    <h5>SITE MAP</h5>
    <ul><li>HOME</li><li>ABOUT US</li><li>BUSINESS UNITS</li><li>SERVICES</li><li>LOCATIONS</li><li>CONTACT US</li></ul>
  </div>
  <div class="events abs">
    <h5>UP COMING EVENTS</h5>
    <ul>
      <li>Monday 07:00 AM — 07:00 PM</li>
      <li>Tuesday 07:00 AM — 07:00 PM</li>
      <li>Wednesday 07:00 AM — 07:00 PM</li>
      <li>Thursday 07:00 AM — 07:00 PM</li>
    </ul>
  </div>
  <div class="contact abs">
    <h5>OUR CONTACT INFORMATION</h5>
    <ul>
      <li><span class="ico"><svg width="8" height="11" viewBox="0 0 8 11"><path d="M4 0a4 4 0 0 1 4 4c0 3-4 7-4 7S0 7 0 4a4 4 0 0 1 4-4z" fill="#fff"/><circle cx="4" cy="4" r="1.5" fill="#d42a2a"/></svg></span>Quelbrant International</li>
      <li class="indent">51, Larkspur Ave New York&nbsp; NY</li>
      <li><span class="ico"><svg width="6" height="10" viewBox="0 0 6 10"><rect x=".6" y=".6" width="4.8" height="8.8" rx="1" stroke="#fff" stroke-width="1.2" fill="none"/></svg></span>(555) 010 45 22</li>
      <li><span class="ico"><svg width="10" height="7" viewBox="0 0 12 8"><rect width="12" height="8" fill="#fff"/><path d="M0 0l6 4.5L12 0" stroke="#d42a2a" fill="none"/></svg></span>info@quelbrant-example.com</li>
    </ul>
  </div>
</footer>

<div class="bottom-bar abs">
  <p class="copyright abs">Copyrights © 2014 quelbrant-example.com - All Rights Reserved</p>
  <div class="follow abs"><span class="label">Follow Us</span><span class="social-dot"></span><span class="social-dot"></span><span class="social-dot"></span></div>
</div>

</body>
</html>
```